KBT Business Cards

We require business cards for our business. We would like a matte black back to the card, with our logo centred in the middle. The front side of the card is open to design.

Target Market(s)

Clients looking for legal services (professional)

Industry/Entity Type

Legal

Contact Information for Business Card

Doran Kelbrath
Partner
Mobile: 0461 738 524
Email: doran@kbtlaw.co
Website: www.kbtlaw.co
Level 3, 118 Wendmore Street
Sydney NSW 2000

Font styles to use
Other font styles liked:
• Avenir

Colors
f04a50
ffffff
1b1b1b

Requirements
Must have
• Black back with logo included in the centre of the card.
• Our font is Avenir.

```html
<!DOCTYPE html>
<html lang="en">
<head>
<meta charset="utf-8">
<title>Kelbrath Bowen Tate – Business Cards</title>
<link href="https://fonts.googleapis.com/css2?family=Nunito+Sans:wght@400;600;700;800&display=swap" rel="stylesheet">
<style>
  :root {
    --ink: #1b1b1b;
    --red: #c8213f;
    --grey: #5a5a5a;
    --grey-light: #a8a8a8;
    --paper: #ffffff;
    --backdrop: #e6e6e6;
  }
  * { box-sizing: border-box; margin: 0; padding: 0; }
  html, body {
    width: 1200px; height: 892px; overflow: hidden;
    background: var(--backdrop);
    font-family: "Nunito Sans", "Avenir", sans-serif;
    color: var(--ink);
  }
  .canvas { position: relative; width: 1200px; height: 892px; }
  .card {
    position: absolute; left: 290px; width: 620px; height: 379px;
    background: var(--paper);
    box-shadow: 0 6px 18px rgba(0,0,0,.18);
  }
  .card--back { top: 48px; background: var(--ink); }
  .card--front { top: 465px; }

  /* Back side: matte black with centred name */
  .brand {
    position: absolute; left: 50%; top: 50%;
    transform: translate(-50%, -62%);
    display: flex; align-items: center; gap: 16px;
  }
  .brand__square { width: 24px; height: 24px; background: var(--red); flex: none; }
  .brand__name {
    font-weight: 800; font-size: 26px; line-height: 1.04;
    text-transform: uppercase; color: var(--paper); letter-spacing: .01em;
  }
  .card__url {
    position: absolute; left: 0; right: 0; top: 292px; text-align: center;
    font-size: 14px; letter-spacing: .75em; color: var(--grey-light);
    text-transform: uppercase; padding-left: .75em;
  }

  /* Front side */
  .firm {
    position: absolute; left: 54px; top: 92px;
    font-weight: 800; font-size: 33px; line-height: 1.02;
    text-transform: uppercase; color: var(--ink);
  }
  .person {
    position: absolute; right: 70px; top: 110px; text-align: right;
  }
  .person__name { font-weight: 800; font-size: 19px; color: var(--red); }
  .person__role { font-size: 13px; color: var(--ink); margin-top: -2px; }
  .contact {
    position: absolute; left: 54px; top: 238px;
    font-size: 14px; color: var(--grey); line-height: 1.35;
  }
  .contact__address { margin-bottom: 8px; }
  .contact__row { display: flex; align-items: center; gap: 10px; }
  .contact__icon { width: 14px; height: 14px; flex: none; }
</style>
</head>
<body>
<main class="canvas">

  <section class="card card--back" aria-label="Card back">
    <div class="brand">
      <span class="brand__square"></span>
      <div class="brand__name">Kelbrath<br>Bowen<br>Tate</div>
    </div>
    <p class="card__url">www.kbtlaw.co</p>
  </section>

  <section class="card card--front" aria-label="Card front">
    <div class="firm">Kelbrath<br>Bowen<br>Tate</div>

    <div class="person">
      <p class="person__name">Doran Kelbrath</p>
      <p class="person__role">Partner</p>
    </div>

    <div class="contact">
      <p class="contact__address">Level 3, 118 Wendmore Street<br>Sydney NSW 2000</p>
      <p class="contact__row">
        <svg class="contact__icon" viewBox="0 0 14 14" aria-hidden="true">
          <rect x="3" y="1" width="8" height="12" rx="1.5" fill="none" stroke="var(--red)" stroke-width="1.6"/>
          <circle cx="7" cy="10.5" r=".9" fill="var(--red)"/>
        </svg>
        0461 738 524
      </p>
      <p class="contact__row">
        <svg class="contact__icon" viewBox="0 0 14 14" aria-hidden="true">
          <rect x="1" y="3" width="12" height="8.5" fill="var(--red)"/>
          <path d="M1 3 L7 8 L13 3" fill="none" stroke="#fff" stroke-width="1.2"/>
        </svg>
        doran@kbtlaw.co
      </p>
      <p class="contact__row">
        <svg class="contact__icon" viewBox="0 0 14 14" aria-hidden="true">
          <circle cx="7" cy="7" r="6" fill="var(--red)"/>
          <ellipse cx="7" cy="7" rx="2.6" ry="6" fill="none" stroke="#fff" stroke-width="1"/>
          <line x1="1" y1="7" x2="13" y2="7" stroke="#fff" stroke-width="1"/>
        </svg>
        www.kbtlaw.co
      </p>
    </div>
  </section>

</main>
</body>
</html>
```